Harrow Grading LLC business card design

Excavation company business cards

Contact Information for Business Card

Harrow Grading LLC cell phone 208-417-6290 office phone 208-319-4856 harrowgradingllc@maplecove.com Driveways, site prep, retaining walls, septic systems, rock delivery

Colors

Designer to choose colors to be used in the design.

```html
<!DOCTYPE html>
<html lang="en">
<head>
<meta charset="utf-8">
<title>Harrow Grading LLC – Business Card</title>
<link href="https://fonts.googleapis.com/css2?family=Roboto:wght@400;500;700&display=swap" rel="stylesheet">
<style>
  :root {
    --orange: #ec6f24;
    --slate: #626262;
    --slate-light: #7a7a7a;
    --paper: #ffffff;
    --ink: #2b2b2b;
    --backdrop: #c9c9c9;
  }
  * { margin: 0; padding: 0; box-sizing: border-box; }
  html, body { width: 1200px; height: 788px; overflow: hidden; }
  body {
    background: var(--backdrop);
    font-family: "Roboto", Arial, sans-serif;
    position: relative;
  }
  .card {
    position: absolute;
    width: 540px;
    height: 309px;
    border-radius: 22px;
    overflow: hidden;
    box-shadow: 0 10px 24px rgba(0,0,0,.22);
  }
  .card--front { left: 50px; top: 100px; background: var(--paper); }
  .card--back { left: 610px; top: 380px; background: var(--slate); }

  .front-swoosh { position: absolute; inset: 0; width: 100%; height: 100%; }

  .holder { position: absolute; right: 34px; top: 22px; text-align: right; color: var(--paper); }
  .holder__name { font-weight: 700; font-size: 22px; letter-spacing: .5px; }
  .holder__title { font-size: 14px; margin-top: 2px; }

  .brand {
    display: flex; align-items: center; gap: 10px;
    color: var(--orange); font-weight: 700;
  }
  .brand__dot { background: var(--orange); border-radius: 50%; flex: none; }
  .card--front .brand { position: absolute; right: 34px; top: 128px; font-size: 24px; }
  .card--front .brand__dot { width: 14px; height: 14px; }

  .contact {
    position: absolute; left: 34px; bottom: 26px;
    color: var(--ink); font-size: 14px; line-height: 1.45;
  }
  .contact__address { margin-bottom: 8px; }
  .contact__row { display: flex; align-items: center; gap: 8px; }
  .contact__icon { width: 12px; height: 12px; fill: var(--orange); flex: none; }

  .card--back .brand {
    position: absolute; left: 0; right: 0; top: 112px;
    justify-content: center; font-size: 34px;
  }
  .card--back .brand__dot { width: 18px; height: 18px; }
  .services {
    position: absolute; left: 0; right: 0; bottom: 40px;
    text-align: center; color: var(--paper); font-size: 15px; font-weight: 500;
  }
  .services__sep { color: var(--orange); margin: 0 6px; }
</style>
</head>
<body>

<section class="card card--front" aria-label="Business card front">
  <svg class="front-swoosh" viewBox="0 0 540 309" preserveAspectRatio="none" aria-hidden="true">
    <path d="M0,70 C140,92 280,118 420,106 C480,100 525,78 540,40 L540,56 C520,100 470,120 410,124 C270,134 130,108 0,88 Z" fill="var(--slate)"/>
    <path d="M0,0 H540 V30 C520,78 475,96 410,102 C270,112 130,86 0,66 Z" fill="var(--orange)"/>
  </svg>

  <div class="holder">
    <div class="holder__name">DALEN MARSH</div>
    <div class="holder__title">Founder</div>
  </div>

  <div class="brand"><span class="brand__dot"></span>Harrow Grading LLC</div>

  <div class="contact">
    <div class="contact__address">4587 Quarry Lane<br>Ridgefield ID 83401</div>
    <div class="contact__row">
      <svg class="contact__icon" viewBox="0 0 24 24"><path d="M6.6 10.8a15.1 15.1 0 0 0 6.6 6.6l2.2-2.2c.3-.3.7-.4 1-.2 1.1.4 2.3.6 3.6.6.6 0 1 .4 1 1V20c0 .6-.4 1-1 1A17 17 0 0 1 3 4c0-.6.4-1 1-1h3.5c.6 0 1 .4 1 1 0 1.3.2 2.5.6 3.6.1.3 0 .7-.2 1z"/></svg>
      <span>208-319-4856</span>
    </div>
    <div class="contact__row">
      <svg class="contact__icon" viewBox="0 0 24 24"><path d="M7 1h10a2 2 0 0 1 2 2v18a2 2 0 0 1-2 2H7a2 2 0 0 1-2-2V3a2 2 0 0 1 2-2zm0 3v14h10V4z"/></svg>
      <span>208-417-6290</span>
    </div>
    <div class="contact__row">
      <svg class="contact__icon" viewBox="0 0 24 24"><path d="M2 5h20v14H2zm2 2v.5l8 5 8-5V7z"/></svg>
      <span>harrowgradingllc@maplecove.com</span>
    </div>
    <div class="contact__row">
      <svg class="contact__icon" viewBox="0 0 24 24"><path d="M12 2a10 10 0 1 0 0 20 10 10 0 0 0 0-20zm0 2c1 1.4 1.8 3.2 2 5h-4c.2-1.8 1-3.6 2-5zM4.3 13h3.8c.1 1.9.6 3.7 1.4 5.3A8 8 0 0 1 4.3 13zm0-2a8 8 0 0 1 5.2-6.3C8.7 6.3 8.2 8.1 8.1 11zm7.7 9c-1-1.4-1.8-3.2-2-5h4c-.2 1.8-1 3.6-2 5zm2.5-1.7c.8-1.6 1.3-3.4 1.4-5.3h3.8a8 8 0 0 1-5.2 5.3zm1.4-7.3c-.1-2.9-.6-4.7-1.4-6.3A8 8 0 0 1 19.7 11z"/></svg>
      <span>www.harrowgradingllc.com</span>
    </div>
  </div>
</section>

<section class="card card--back" aria-label="Business card back">
  <div class="brand"><span class="brand__dot"></span>Harrow Grading LLC</div>
  <p class="services">
    Driveways<span class="services__sep">•</span>Site Prep<span class="services__sep">•</span>Retaining Walls<span class="services__sep">•</span>Septic Systems<span class="services__sep">•</span>Rock Delivery
  </p>
</section>

</body>
</html>
```